All-Natural Head Lice Removal company

I need a business card with my pre-existing logo. We are a new company located in Portland Oregon that goes into peoples homes to help with head lice removal. My products and approach are all- natural and also will be around children.On my current logo we used Teal Bl and the color Green. I am open to new ideas just want it simple and creative

Target Market(s)

my biggest market is families of school aged children

Industry/Entity Type

Business

Contact Information for Business Card

see upload for details from previous business card

Font styles to use
Serif

Colors
33a6d7
9bcb3b
f37122

Requirements
Must have
• Basic information/ logo put into a creative format that is catching to the eye
Nice to have
• creative

```html
<!DOCTYPE html>
<html lang="en">
<head>
<meta charset="utf-8">
<title>Nitwise Business Card</title>
<link href="https://fonts.googleapis.com/css2?family=Open+Sans:wght@400;600;700&family=Signika:wght@600;700&display=swap" rel="stylesheet">
<style>
  :root {
    --page: #e8e5e0;
    --card: #fbfbfb;
    --card-shade: #eeeeee;
    --green: #7dc242;
    --blue: #33a6d7;
    --ink: #2f2f2f;
    --heading: #4a4a4a;
    --white: #ffffff;
  }
  * { margin: 0; padding: 0; box-sizing: border-box; }
  html, body { width: 1200px; height: 1023px; overflow: hidden; }
  body {
    background: var(--page);
    font-family: "Open Sans", sans-serif;
    position: relative;
  }
  .card {
    position: absolute;
    background: linear-gradient(135deg, var(--white) 0%, var(--card) 50%, var(--card-shade) 100%);
    border-radius: 26px;
    box-shadow: 0 6px 18px rgba(0,0,0,0.18);
    overflow: hidden;
  }
  /* Front */
  .card-front { left: 70px; top: 70px; width: 660px; height: 380px; }
  .front-tagline {
    position: absolute; left: 44px; top: 46px; width: 400px;
    font-family: "Signika", sans-serif; font-weight: 700;
    font-size: 30px; line-height: 1.25; color: var(--heading);
  }
  .blue-strip {
    position: absolute; right: 40px; top: 0; width: 60px; height: 200px;
    background: var(--blue);
  }
  .green-band {
    position: absolute; left: 0; right: 0; top: 200px; height: 72px;
    background: var(--green);
  }
  .person { position: absolute; left: 44px; top: 210px; color: var(--white); }
  .person-name { font-family: "Signika", sans-serif; font-weight: 700; font-size: 24px; line-height: 1.1; }
  .person-role { font-family: "Signika", sans-serif; font-weight: 600; font-size: 14px; margin-top: 4px; }
  .contacts { position: absolute; left: 44px; top: 290px; font-size: 15px; line-height: 1.5; color: var(--ink); }
  .contacts .label { color: var(--green); font-weight: 700; }
  .contacts .accent { color: var(--green); }
  .brand {
    position: absolute; display: flex; align-items: center; gap: 8px;
  }
  .brand-dot { width: 46px; height: 46px; border-radius: 50%; background: var(--green); flex: none; }
  .brand-name { font-family: "Open Sans", sans-serif; font-weight: 700; color: var(--ink); }
  .card-front .brand { right: 22px; top: 118px; }
  .card-front .brand-name { font-size: 30px; }
  /* Back */
  .card-back { left: 520px; top: 560px; width: 600px; height: 390px; }
  .card-back .brand { left: 50%; top: 72px; transform: translateX(-50%); }
  .card-back .brand-dot { width: 70px; height: 70px; }
  .card-back .brand-name { font-size: 46px; }
  .back-text {
    position: absolute; left: 0; right: 0; top: 210px;
    text-align: center; color: var(--ink); font-size: 18px; line-height: 1.6;
  }
  .back-text .accent { color: var(--blue); }
</style>
</head>
<body>
  <section class="card card-front" aria-label="Business card front">
    <div class="blue-strip"></div>
    <div class="green-band"></div>
    <h1 class="front-tagline">All Natural In-Home Lice Removal Services</h1>
    <div class="brand">
      <span class="brand-dot"></span>
      <span class="brand-name">Nitwise</span>
    </div>
    <div class="person">
      <div class="person-name">Mara Ellison</div>
      <div class="person-role">Owner</div>
    </div>
    <div class="contacts">
      <div><span class="label">P :</span> 1-555-014-NITS (6487)</div>
      <div><span class="label">E :</span> mara@nitwisehome.com</div>
      <div><span class="label">W :</span> www.<span class="accent">nitwisehome</span>.com</div>
    </div>
  </section>

  <section class="card card-back" aria-label="Business card back">
    <div class="brand">
      <span class="brand-dot"></span>
      <span class="brand-name">Nitwise</span>
    </div>
    <div class="back-text">
      <div>Try Nitwise Today and Be Lice Free Tomorrow!</div>
      <div>All Natural In-Home Lice Removal Servise</div>
      <div>www.<span class="accent">nitwisehome</span>.com</div>
    </div>
  </section>
</body>
</html>
```